Poster

I need a poster for my business, www.coastalsupperroutesnerja.example which some information about the most important activities (Sangria Tasting, Iberian Ham, Charcuteries & Sherry Wine Tasting, Sailboat Experiences and Picnic Experiences). A3 Format. Social media included (@coastalsupperroutescsr), contact information included.

```html
<!DOCTYPE html>
<html lang="en">
<head>
<meta charset="utf-8">
<title>Marbella &amp; Estepona – Coastal Supper Routes</title>
<link rel="stylesheet" href="https://fonts.googleapis.com/css2?family=Bebas+Neue&family=Great+Vibes&family=Montserrat:wght@500;700&family=Poppins:wght@400;500&display=swap">
<style>
:root{
  --backdrop:#cdcdcd;
  --board:#1d1915;
  --board-edge:#141110;
  --amber:#f5a41c;
  --white:#ffffff;
  --text-soft:#e9e4de;
  --rule:#a8741c;
}
*{margin:0;padding:0;box-sizing:border-box}
html,body{width:1200px;height:1033px;overflow:hidden;background:var(--backdrop)}
.poster{
  position:absolute;left:293px;top:85px;width:614px;height:867px;
  background:radial-gradient(ellipse at 50% 45%,#2a231d 0%,var(--board) 55%,var(--board-edge) 100%);
  overflow:hidden;box-shadow:0 6px 18px rgba(0,0,0,.35);
}
.dish{position:absolute;border-radius:50%}
.dish-potatoes{left:-40px;top:10px;width:160px;height:215px;background:radial-gradient(circle at 55% 50%,#c98a3a 0%,#8a5220 45%,#1a1512 72%)}
.dish-greens{left:468px;top:-20px;width:170px;height:180px;border-radius:40%;background:radial-gradient(circle at 62% 45%,#5d8a32 0%,#8a5a33 45%,#b58350 62%,rgba(0,0,0,0) 72%)}
.dish-mushroom{left:555px;top:185px;width:80px;height:110px;background:radial-gradient(circle at 60% 50%,#7a5a3e 0%,#3b2a1f 55%,#111 72%)}
.dish-veg{left:-30px;top:725px;width:200px;height:190px;background:radial-gradient(circle at 50% 55%,#e0a131 0%,#b9581f 40%,#2c2a26 70%)}
.dish-salad{left:178px;top:790px;width:130px;height:120px;background:radial-gradient(circle at 50% 55%,#c8cfb5 0%,#7c8e5e 45%,#262421 70%)}
.dish-chicken{left:330px;top:720px;width:320px;height:200px;background:radial-gradient(ellipse at 55% 60%,#c4762d 0%,#8b4619 45%,#2a211b 72%)}

.enjoy{position:absolute;left:213px;top:26px;font:400 62px/1 'Great Vibes',cursive;color:var(--amber)}
.headline{position:absolute;left:112px;width:395px;text-align:center;font:400 125px/1 'Bebas Neue',sans-serif;color:var(--white);letter-spacing:-1px}
.headline.top{top:78px}
.headline.bottom{top:178px}
.amp{position:absolute;left:297px;top:169px;width:38px;height:38px;border-radius:50%;background:var(--amber);color:var(--board);font:700 22px/38px 'Montserrat',sans-serif;text-align:center}
.tagline{position:absolute;left:112px;top:292px;width:395px;text-align:center;font:700 14.5px/1 'Montserrat',sans-serif;letter-spacing:5.6px;color:var(--amber);white-space:nowrap}

.activity{position:absolute;top:338px;width:116px;text-align:center}
.activity svg{display:block;margin:0 auto;width:42px;height:42px}
.activity h2{margin-top:14px;font:400 15.5px/16px 'Bebas Neue',sans-serif;color:var(--amber);letter-spacing:.2px}
.activity p{width:86px;margin:10px auto 0;font:500 7.8px/9.7px 'Poppins',sans-serif;color:var(--text-soft)}
.divider{position:absolute;top:391px;width:1px;height:220px;background:var(--rule);opacity:.75}

.brand{position:absolute;left:88px;top:655px;display:flex;align-items:center;gap:8px}
.brand-mark{width:14px;height:14px;background:var(--amber)}
.brand-name{font:400 19px/18px 'Bebas Neue',sans-serif;color:var(--white)}
.follow{position:absolute;left:243px;top:666px;display:flex;align-items:center;gap:8px;color:var(--white)}
.follow small{font:500 9px 'Montserrat',sans-serif;letter-spacing:1.5px}
.follow .dot{width:12px;height:12px;border-radius:3px;background:var(--amber)}
.follow span{font:500 13.5px 'Montserrat',sans-serif;letter-spacing:1.3px}
.site{position:absolute;left:243px;top:689px;font:700 13.6px 'Montserrat',sans-serif;letter-spacing:.9px;color:var(--white);white-space:nowrap}
.site b{color:var(--amber);font-weight:700}
</style>
</head>
<body>
<main class="poster">
  <div class="dish dish-potatoes" role="img" aria-label="Pan of roasted potatoes, sausage and olives"></div>
  <div class="dish dish-greens" role="img" aria-label="Bowl of broccoli, tomatoes and sliced chicken on a wooden board"></div>
  <div class="dish dish-mushroom" role="img" aria-label="Small bowl of sautéed mushrooms and onions"></div>
  <div class="dish dish-veg" role="img" aria-label="Pan of mixed vegetables with corn and carrots"></div>
  <div class="dish dish-salad" role="img" aria-label="Bowl of cabbage and cucumber salad"></div>
  <div class="dish dish-chicken" role="img" aria-label="Roast chicken with tomatoes and basil in a cast-iron pot"></div>

  <div class="enjoy">Enjoy</div>
  <h1 class="headline top">Marbella</h1>
  <div class="amp">&amp;</div>
  <div class="headline bottom">Estepona</div>
  <div class="tagline">WITH COASTAL SUPPER ROUTES</div>

  <section class="activity" style="left:24px">
    <svg viewBox="0 0 42 42" fill="none" stroke="#fff" stroke-width="1.4"><path d="M8 22h22a11 11 0 0 1-22 0z"/><path d="M22 22l4-14h6"/><path d="M12 22c2-5 8-6 10-2"/></svg>
    <h2>Sangria<br>Tasting</h2>
    <p>During this experience, you will try four distinct types of authentic Sangria, each crafted with different wines and fresh locally sourced ingredients. As you sip, immerse yourself in the vibrant atmosphere of Estepona, enjoying the flavors of marinated olives and local cheese included with your booking.</p>
  </section>
  <div class="divider" style="left:140px"></div>

  <section class="activity" style="left:136px">
    <svg viewBox="0 0 42 42" fill="none" stroke="#fff" stroke-width="1.4"><ellipse cx="23" cy="22" rx="14" ry="11"/><ellipse cx="18" cy="22" rx="10" ry="10"/><path d="M14 20c3-4 8-4 10 0-2 3-7 3-10 0z"/></svg>
    <h2>Iberian<br>Ham</h2>
    <p>Indulge in the rich flavors of Spain with our Iberian Charcuteries &amp; Sherry Wine Tasting. Sample two premium Iberian hams, three distinct sausages, and a variety of olives, all perfectly paired with a selection of Sherry wines.</p>
  </section>
  <div class="divider" style="left:251px"></div>

  <section class="activity" style="left:251px">
    <svg viewBox="0 0 42 42" fill="none" stroke="#fff" stroke-width="1.4"><path d="M24 4h4v8l2 4v22h-8V16l2-4z"/><path d="M31 22h7c0 5-2 8-3.5 8S31 27 31 22zM34.5 30v8"/><circle cx="10" cy="30" r="3"/><circle cx="16" cy="30" r="3"/><circle cx="13" cy="35" r="3"/><path d="M13 27v-6"/></svg>
    <h2>Charcuteries<br>&amp; Sherry<br>Wine Tasting</h2>
    <p>ndulge in the rich flavors of Spain with our Iberian Charcuteries &amp; Sherry Wine Tasting. Sample two premium Iberian hams, three distinct sausages, and a variety of olives, all perfectly paired with a selection of Sherry wines.</p>
  </section>
  <div class="divider" style="left:367px"></div>

  <section class="activity" style="left:367px">
    <svg viewBox="0 0 42 42" fill="none" stroke="#fff" stroke-width="1.4"><path d="M20 4v24"/><path d="M20 6l10 18H20"/><path d="M18 10L10 24h8"/><path d="M7 28h28l-4 5H11z"/><path d="M5 37c3-2 5 2 8 0s5 2 8 0 5 2 8 0 5 2 8 0"/></svg>
    <h2>Sailboat<br>Experiences</h2>
    <p>The Sailboat Sangria Tasting Experience is a unique and enchanting journey where you can relax and unwind while sailing along the beautiful coast of Estepona. Sip on exquisite artisanal sangria and enjoy gourmet appetizers in a serene and picturesque setting.</p>
  </section>
  <div class="divider" style="left:483px"></div>

  <section class="activity" style="left:481px">
    <svg viewBox="0 0 42 42" fill="none" stroke="#fff" stroke-width="1.4"><path d="M6 20h30l-4 16H10z"/><path d="M9 26h24M11 31h20"/><path d="M12 20c0-8 18-8 18 0"/><path d="M17 18l3-8 4 8"/></svg>
    <h2>Picnic<br>Experiences</h2>
    <p>Indulge in a unique morning retreat with our Picnic Brunch Experience from Estepona to Cala Dorada. Select from our gourmet picnic basket filled with freshly baked pastries, artisanal cheeses, cured meats, seasonal fruits, and decadent desserts.</p>
  </section>

  <div class="brand">
    <div class="brand-mark"></div>
    <div class="brand-name">Coastal Supper<br>Routes Nerja</div>
  </div>
  <div class="follow"><small>follow us on</small><div class="dot"></div><span>@coastalsupperroutescsr</span></div>
  <div class="site">www.<b>coastalsupperroutesnerja</b>.example</div>
</main>
</body>
</html>
```